Electrician Letterhead Design MVR

We need some letterhead for our bills and other papers.
Customer address is on the right side (Swiss format)
A4 format

Design should also be applicable on Cards

Target Market(s)

Private Customers, Small Business

Industry/Entity Type

Electrician

Other font styles liked:
• incised 901

Colors
00AB8E
00BBA5
67D7C9
C6EFE9
E9F9F6

```html
<!DOCTYPE html>
<html lang="de">
<head>
<meta charset="utf-8">
<title>MVR Letterhead</title>
<link rel="stylesheet" href="https://fonts.googleapis.com/css2?family=Open+Sans:wght@400;600;700&display=swap">
<style>
  :root {
    --teal-deep: #00AB8E;
    --teal: #00BBA5;
    --teal-light: #67D7C9;
    --teal-pale: #C6EFE9;
    --teal-mist: #E9F9F6;
    --paper: #FFFFFF;
    --backdrop: #E4E4E4;
    --ink: #4A4A4A;
  }
  * { box-sizing: border-box; margin: 0; padding: 0; }
  html, body {
    width: 1200px; height: 800px; overflow: hidden;
    background: var(--backdrop);
    font-family: "Open Sans", sans-serif;
  }
  .letterhead {
    position: absolute; left: 352px; top: 49px;
    width: 496px; height: 702px;
    background: var(--paper);
    box-shadow: 0 2px 10px rgba(0,0,0,0.08);
    overflow: hidden;
  }
  .rule { position: absolute; height: 1.5px; background: var(--teal); }
  .rule--lead { left: 0; width: 26px; top: 92px; }
  .rule--header { left: 142px; width: 196px; top: 92px; }
  .rule--corner { left: 456px; width: 40px; top: 36px; }
  .brand { position: absolute; left: 34px; top: 62px; }
  .brand__name {
    font-weight: 700; font-size: 40px; line-height: 1;
    color: var(--teal-deep); letter-spacing: 1px;
  }
  .brand__tagline {
    font-weight: 700; font-size: 8.5px; color: var(--ink);
    margin-top: 3px; letter-spacing: 0.3px;
  }
  .contact {
    position: absolute; left: 350px; top: 24px;
    font-size: 7px; line-height: 1.45; color: var(--ink);
  }
  .contact__row { display: flex; align-items: center; gap: 4px; }
  .contact__row svg { width: 7px; height: 7px; flex: none; }
  .website {
    position: absolute; right: 30px; bottom: 38px;
    font-size: 8px; font-weight: 600; color: var(--teal-deep);
  }
  .watermark {
    position: absolute; left: 150px; bottom: -60px;
    width: 200px; height: 200px; border-radius: 50%;
    background: var(--teal-mist);
  }
</style>
</head>
<body>
  <main class="letterhead">
    <div class="rule rule--lead"></div>
    <div class="rule rule--header"></div>
    <div class="rule rule--corner"></div>

    <div class="brand">
      <div class="brand__name">MVR</div>
      <div class="brand__tagline">Elektrotechnik Mever GmbH</div>
    </div>

    <address class="contact" style="font-style: normal;">
      <div>Suite 102 Street name,</div>
      <div>State, Zip 2034, Country</div>
      <div class="contact__row">
        <svg viewBox="0 0 10 10"><circle cx="5" cy="5" r="5" fill="var(--teal-deep)"/><path d="M3.2 2.6c.4-.3.8 0 1 .5l.2.5-.5.5c.3.7.8 1.2 1.5 1.5l.5-.5.5.2c.5.2.8.6.5 1-.4.6-1.2.7-2 .2-1-.6-1.9-1.5-2.4-2.5-.4-.8-.3-1.5.2-1.9z" fill="#fff"/></svg>
        <span>+41-4455-667788</span>
      </div>
      <div class="contact__row">
        <svg viewBox="0 0 10 10"><circle cx="5" cy="5" r="5" fill="var(--teal-deep)"/><rect x="2.4" y="3.2" width="5.2" height="3.6" fill="none" stroke="#fff" stroke-width="0.8"/><path d="M2.4 3.2 5 5.2 7.6 3.2" fill="none" stroke="#fff" stroke-width="0.8"/></svg>
        <span>info@mevertechnik.ch</span>
      </div>
    </address>

    <div class="watermark" role="img" aria-label="Faint brand decoration"></div>

    <div class="website">www.mevertechnik.ch</div>
  </main>
</body>
</html>
```